e-commerce store for sport clothing online store "baseball merchandise "web application...

I want to design a UX/UI for my web application website for the online store I will provide you with the following:
1. screen shots of the initial design for the pages>
2. the logo files.
3. The brand guideline file.

the provided files (screen shots) is guideline I want to see CREATIVITY with the UX/UI DESIGN.
PS. PLEASE FOLLOW THE BRANDGUIDE LINE CAREFULLY SPECIALLY THE TYPOGRAPHY & THE COLOR CODES.

PLEASE VISIT THIS WEBSITE brightlane.varomi-qz.com to see more for the screens.

```html
<!DOCTYPE html>
<html lang="en">
<head>
<meta charset="UTF-8">
<title>Checkout</title>
<link href="https://fonts.googleapis.com/css2?family=Titillium+Web:wght@600;700;900&family=Lato:wght@400;700;900&display=swap" rel="stylesheet">
<style>
:root{
  --navy:#0f2148;
  --white:#ffffff;
  --ink:#111111;
  --muted:#333a44;
  --line:#d9d9d9;
  --black:#000000;
  --trunks:#5fb286;
  --trunks-light:#8cc9a6;
  --cap:#c9ccd2;
}
*{margin:0;padding:0;box-sizing:border-box}
html,body{width:1200px;height:2667px;overflow:hidden;background:var(--white)}
.canvas{position:relative;width:1200px;height:2667px;overflow:hidden}
.screen{
  position:absolute;left:0;top:0;width:360px;height:800px;overflow:hidden;
  transform:scale(3.333333);transform-origin:0 0;
  background:var(--white);font-family:'Lato',sans-serif;color:var(--ink);
}
.app-bar{position:absolute;left:0;top:0;width:360px;height:83px;background:var(--navy)}
.app-bar .back{position:absolute;left:23px;top:31px}
.app-bar h1{position:absolute;left:0;right:0;top:29px;text-align:center;color:var(--white);
  font-family:'Titillium Web',sans-serif;font-weight:700;font-size:17px;line-height:22px}
.stepper{position:absolute;left:0;top:118px;width:360px;height:80px}
.stepper .track{position:absolute;left:80px;width:202px;top:19px;height:1.3px;background:var(--navy)}
.step{position:absolute;top:0;width:90px;margin-left:-45px;text-align:center}
.step .dot{width:38px;height:38px;border-radius:50%;background:var(--navy);margin:0 auto;
  color:var(--white);font-family:'Titillium Web',sans-serif;font-weight:700;font-size:20px;line-height:38px}
.step .label{margin-top:5px;font-size:12.5px;line-height:15px;color:var(--navy)}
.section-title{position:absolute;left:14px;top:221px;font-family:'Titillium Web',sans-serif;font-weight:700;font-size:16px}
.item{position:absolute;left:14px;width:332px}
.item .thumb{position:absolute;left:0;top:0;border-radius:4px}
.item .name{position:absolute;left:80px;top:-1px;width:150px;font-family:'Titillium Web',sans-serif;font-weight:700;font-size:14.5px;line-height:18px}
.item .unit{position:absolute;left:80px;font-size:10.5px;line-height:13px;color:var(--muted)}
.item .qty{position:absolute;left:80px;font-size:12.5px;line-height:15px;color:var(--ink)}
.item .price{position:absolute;right:0;top:0;font-family:'Titillium Web',sans-serif;font-weight:700;font-size:15px;color:var(--navy)}
.summary{position:absolute;left:20px;right:20px;top:622px}
.summary .row{display:flex;justify-content:space-between;height:27px;font-size:12.5px;line-height:18px}
.summary .row .value{font-family:'Titillium Web',sans-serif;font-weight:700;color:var(--navy)}
.action-bar{position:absolute;left:2px;right:2px;top:741px;height:59px;background:var(--white);
  border-radius:12px 12px 0 0;box-shadow:0 -1px 4px rgba(0,0,0,.25)}
.place-order{position:absolute;left:10px;right:10px;top:8px;height:47px;background:var(--black);
  border:none;border-radius:4px;color:var(--white);font-family:'Titillium Web',sans-serif;font-weight:700;font-size:14.5px}
</style>
</head>
<body>
<div class="canvas">
<div class="screen">
  <header class="app-bar">
    <svg class="back" width="20" height="20" viewBox="0 0 20 20" aria-label="Back"><path d="M17 10H4M10 3.5L3.5 10 10 16.5" fill="none" stroke="#fff" stroke-width="2.2" stroke-linecap="round" stroke-linejoin="round"/></svg>
    <h1>Checkout</h1>
  </header>

  <nav class="stepper">
    <div class="track"></div>
    <div class="step" style="left:80px"><div class="dot">1</div><div class="label">Shipping<br>Details</div></div>
    <div class="step" style="left:180px"><div class="dot">2</div><div class="label">Payment<br>Details</div></div>
    <div class="step" style="left:282px"><div class="dot">3</div><div class="label">Confirmation</div></div>
  </nav>

  <h2 class="section-title">Items</h2>

  <div class="item" style="top:259px">
    <div class="thumb" role="img" aria-label="Kids swim trunks product photo" style="width:64px;height:64px;background:linear-gradient(135deg,var(--trunks-light),var(--trunks) 60%,#e8e2d6)"></div>
    <div class="name">Splashy Kids Swim Trunks</div>
    <div class="unit" style="top:35px">23.000 KD</div>
    <div class="qty" style="top:52px">Qty: 1</div>
    <div class="price">23.000 KD</div>
  </div>

  <div class="item" style="top:355px">
    <div class="thumb" role="img" aria-label="Trucker cap product photo" style="width:65px;height:67px;border:1px solid var(--line);background:radial-gradient(circle at 50% 50%,var(--cap),#ffffff 72%)"></div>
    <div class="name">Bass Trcker Cap</div>
    <div class="unit" style="top:19px">13.000 KD</div>
    <div class="qty" style="top:52px">Qty: 2</div>
    <div class="price">26.000 KD</div>
  </div>

  <section class="summary">
    <div class="row"><span>Subtotal</span><span class="value">49.000 KD</span></div>
    <div class="row"><span>Delivery Charge</span><span class="value">1.000 KD</span></div>
    <div class="row"><span>Total</span><span class="value">50.000 KD</span></div>
  </section>

  <div class="action-bar">
    <button class="place-order">Place Order</button>
  </div>
</div>
</div>
</body>
</html>
```